International business needs business cards

Our company, DRV Ventures Inc. is in the business of supplying a range construction products with particular emphasis on CEMENT. We have developed our own brand - TORVAN SUPPLIES - with which to infiltrate the market. We are launching our brand of cement (TORVAN Type IS Cement) into the Caribbean which is unlike anything this market has ever seen. A monopoly has existed here for the past 60-odd years and the market has now opened to allow the importation of other brands and consumers are anxious and ready for change/improvement. We are very excited to be launching and want to make a great first impression. We will be conducting workshops and seminars (from government level to the hardware store owners) and we want our business card to give us the strong, confident introduction that we need.

Target Market(s)

construction; builders; engineers; home owners

Industry/Entity Type

Construction

Contact Information for Business Card

Marisol Depree
CEO
cell # 1 555 4180736
Ground floor,Lindell Plaza Suite 2734
George Town,Grand Cayman
Cayman Islands,KY1-4823
EMAIL: m.depree@drvventuresinc.example
web site drvventuresinc.example

COMPANY: skype info drv.ventures.example

second card
Yvette Brannock-Depree
CFO
CELL# 1 555 607 3941
George Town,Grand Cayman
Cayman Islands,KY1-4823
EMAIL: y.brannockdepree@drvventuresinc.example
website drvventuresinc.example

Requirements
Must have
• Business cards must display BOTH logos - DRV is the company and TORVAN is the brand.

```html
<!DOCTYPE html>
<html lang="en">
<head>
<meta charset="utf-8">
<title>DRV Ventures Inc. — Business Cards</title>
<link href="https://fonts.googleapis.com/css2?family=Open+Sans:wght@400;700&display=swap" rel="stylesheet">
<style>
  :root {
    --brand-red: #7b1416;
    --ink: #141414;
    --paper: #ffffff;
    --backdrop: #e9e6e3;
  }
  * { margin: 0; padding: 0; box-sizing: border-box; }
  html, body { width: 1200px; height: 900px; overflow: hidden; }
  body {
    background: var(--backdrop);
    font-family: "Open Sans", Arial, sans-serif;
    position: relative;
  }
  .card { position: absolute; overflow: hidden; }

  /* Front */
  .card-front {
    left: 78px; top: 35px; width: 587px; height: 362px;
    background: var(--paper);
  }
  .card-front .bands { position: absolute; inset: 0; }
  .brand-lockup {
    position: absolute; display: flex; align-items: center; gap: 14px;
  }
  .card-front .brand-lockup { left: 170px; top: 32px; }
  .brand-mark { width: 88px; height: 88px; flex: none; }
  .card-front .brand-mark { background: var(--brand-red); }
  .brand-name { font-weight: 700; font-size: 30px; line-height: 1.1; }
  .card-front .brand-name { color: var(--ink); }

  .holder {
    position: absolute; left: 40px; top: 197px; color: var(--paper);
  }
  .holder-name { font-weight: 700; font-size: 20px; line-height: 1.2; }
  .holder-role { font-size: 15px; margin-top: 4px; }

  .address {
    position: absolute; left: 40px; top: 260px; color: var(--paper);
    font-size: 16px; line-height: 24px; font-style: normal;
  }
  .contacts {
    position: absolute; right: 36px; top: 263px; color: var(--paper);
    font-size: 15px; line-height: 24px; list-style: none; text-align: right;
  }
  .contacts li { display: flex; align-items: center; justify-content: flex-end; gap: 8px; }
  .contacts svg { width: 12px; height: 12px; fill: var(--paper); flex: none; }

  /* Back */
  .card-back {
    left: 388px; top: 505px; width: 567px; height: 352px;
    background: var(--brand-red);
  }
  .card-back .brand-lockup { left: 150px; top: 120px; }
  .card-back .brand-mark { background: var(--paper); }
  .card-back .brand-name { color: var(--paper); }
  .product-brand {
    position: absolute; left: 247px; top: 263px; width: 73px; height: 64px;
    background: var(--paper); color: var(--brand-red);
    display: flex; align-items: center; justify-content: center;
    font-weight: 700; font-size: 13px; letter-spacing: 0.5px;
  }
</style>
</head>
<body>

<section class="card card-front" aria-label="Business card front">
  <svg class="bands" width="587" height="362" viewBox="0 0 587 362" aria-hidden="true">
    <polygon points="0,189 384,189 414,153 587,153 587,362 0,362" fill="#7b1416"/>
    <polygon points="0,160 400,160 382,187 0,187" fill="#141414"/>
  </svg>

  <div class="brand-lockup">
    <span class="brand-mark"></span>
    <span class="brand-name">DRV Ventures Inc.</span>
  </div>

  <div class="holder">
    <div class="holder-name">Marisol Depree</div>
    <div class="holder-role">CEO</div>
  </div>

  <address class="address">
    Ground floor, Lindell Plaza Suite 2734<br>
    George Town, Grand Cayman<br>
    Cayman Islands, KY1-4823
  </address>

  <ul class="contacts">
    <li>1 555 4180736
      <svg viewBox="0 0 24 24"><path d="M6.6 10.8a15 15 0 0 0 6.6 6.6l2.2-2.2a1 1 0 0 1 1-.25 11.4 11.4 0 0 0 3.6.57 1 1 0 0 1 1 1V20a1 1 0 0 1-1 1A17 17 0 0 1 3 4a1 1 0 0 1 1-1h3.5a1 1 0 0 1 1 1c0 1.25.2 2.45.57 3.57a1 1 0 0 1-.25 1z"/></svg>
    </li>
    <li>m.depree@drvventuresinc.example
      <svg viewBox="0 0 24 24"><path d="M2 5h20v14H2zM4 7v.5l8 5 8-5V7l-8 5z"/></svg>
    </li>
    <li>www.drvventuresinc.example
      <svg viewBox="0 0 24 24"><circle cx="12" cy="12" r="10"/></svg>
    </li>
  </ul>
</section>

<section class="card card-back" aria-label="Business card back">
  <div class="brand-lockup">
    <span class="brand-mark"></span>
    <span class="brand-name">DRV Ventures Inc.</span>
  </div>
  <div class="product-brand">TORVAN</div>
</section>

</body>
</html>
```